Advertising company unique advertising platform

we need a logo design for a new company based in Australia Melbourne. We develop innovated advertising platform where consumer can use this platform to get regular discount, as business owner they can use this platform for free advertisement. Payment for this advertisement platform only payable every two weeks, when I generate revenue for their business

Industry/Entity Type

Advertising

Contact Information for Business Card

Dale Morven | Co-Founder |Managing Director
Suite 718 240 Wattlebrook Lane Melbourne Vic 3000

ABN 38 614 207 923
Tel: +61 0487 259 318 | Email: dale.morven@plivorantu.com

Font styles to use
Decorative
Script

Requirements
Must have
• Try few different design and some round corner business card
Should not have
• One round corner business card...try 4 different colour background not only black, make sure two side is designed. Be creative so imagine you are giving this to a client make sure has wow factor, if you can also try one design with engrave like all the logo, words look 3d feel
• The word Advertising Platform use attached file font

```html
<!DOCTYPE html>
<html lang="en">
<head>
<meta charset="utf-8">
<title>Tallowfen Exchange – Business Card</title>
<link rel="stylesheet" href="https://fonts.googleapis.com/css2?family=Marcellus&family=Montserrat:wght@400;500;600&display=swap">
<style>
  :root {
    --page: #e9e9e9;
    --ink-dark: #2b2b2b;
    --ink-white: #ffffff;
    --brand-orange: #f0892a;
    --brand-red: #e5472b;
    --text-dark: #2a2a2a;
    --text-light: #f2f2f2;
    --silver: #9a9a9a;
  }
  * { box-sizing: border-box; margin: 0; padding: 0; }
  html, body { width: 1200px; height: 859px; overflow: hidden; }
  body {
    background: var(--page);
    font-family: "Montserrat", sans-serif;
    display: flex;
    align-items: center;
    justify-content: center;
    gap: 40px;
  }
  .card {
    position: relative;
    width: 560px;
    height: 320px;
    border-radius: 16px;
    overflow: hidden;
    box-shadow: 0 6px 18px rgba(0,0,0,0.18);
  }
  .card--back {
    background: var(--ink-dark);
    display: flex;
    align-items: center;
    justify-content: center;
  }
  .brand {
    display: flex;
    align-items: center;
    gap: 14px;
  }
  .brand__dot {
    width: 34px; height: 34px;
    border-radius: 50%;
    background: var(--brand-orange);
  }
  .brand__name {
    font-family: "Montserrat", sans-serif;
    font-weight: 600;
    font-size: 30px;
    color: var(--silver);
    letter-spacing: 0.5px;
  }
  .card--front { background: var(--ink-white); }
  .front__shape { position: absolute; inset: 0; }
  .front__brand {
    position: absolute;
    left: 30px; top: 44px;
  }
  .front__brand .brand__dot { width: 28px; height: 28px; }
  .front__brand .brand__name { font-size: 22px; color: var(--brand-orange); }
  .address {
    position: absolute;
    left: 34px; top: 150px;
    font-size: 13px;
    line-height: 1.35;
    font-weight: 500;
    color: var(--text-dark);
    letter-spacing: 0.4px;
  }
  .contact {
    position: absolute;
    right: 24px; top: 138px;
    text-align: right;
    color: var(--text-light);
  }
  .contact__name {
    font-family: "Marcellus", serif;
    font-size: 22px;
    color: var(--brand-orange);
    letter-spacing: 1px;
    line-height: 1;
  }
  .contact__role {
    font-family: "Marcellus", serif;
    font-size: 10px;
    letter-spacing: 0.3px;
    margin: 4px 0 5px;
  }
  .contact__line {
    font-size: 12px;
    font-weight: 500;
    letter-spacing: 0.4px;
    line-height: 1.55;
    display: flex;
    justify-content: flex-end;
    align-items: center;
    gap: 8px;
  }
  .contact__label { color: var(--brand-orange); font-weight: 600; }
  .contact__icon { width: 11px; height: 11px; }
</style>
</head>
<body>

  <section class="card card--back" aria-label="Card back">
    <div class="brand">
      <span class="brand__dot"></span>
      <span class="brand__name">Tallowfen Exchange</span>
    </div>
  </section>

  <section class="card card--front" aria-label="Card front">
    <svg class="front__shape" viewBox="0 0 560 320" aria-hidden="true">
      <defs>
        <linearGradient id="swoosh" x1="1" y1="0" x2="0" y2="1">
          <stop offset="0" stop-color="#e5472b"/>
          <stop offset="0.45" stop-color="#f29a32"/>
          <stop offset="1" stop-color="#e5472b"/>
        </linearGradient>
      </defs>
      <path d="M560,64 C440,64 378,86 346,130 C314,180 296,252 0,258 L0,320 L560,320 Z" fill="url(#swoosh)"/>
      <path d="M560,74 C440,74 386,96 356,140 C326,190 304,262 0,268 L0,320 L560,320 Z" fill="#2b2b2b"/>
      <path d="M560,74 C440,74 386,96 356,140 C326,190 304,262 0,268" fill="none" stroke="#ffffff" stroke-width="1.5"/>
    </svg>

    <div class="brand front__brand">
      <span class="brand__dot"></span>
      <span class="brand__name">Tallowfen Exchange</span>
    </div>

    <p class="address">Suite 718 240 Wattlebrook Lane<br>Melbourne Vic 3000</p>

    <div class="contact">
      <p class="contact__name">DALE MORVEN</p>
      <p class="contact__role">|CO-FOUNDER | MANAGING DIRECTOR</p>
      <p class="contact__line"><span><span class="contact__label">ABN:</span> 38 614 207 923</span></p>
      <p class="contact__line">+61 0487 259 318
        <svg class="contact__icon" viewBox="0 0 24 24" aria-hidden="true"><path fill="#f0892a" d="M6.6 10.8a15.1 15.1 0 0 0 6.6 6.6l2.2-2.2a1 1 0 0 1 1-.25 11.4 11.4 0 0 0 3.6.57 1 1 0 0 1 1 1V20a1 1 0 0 1-1 1A17 17 0 0 1 3 4a1 1 0 0 1 1-1h3.5a1 1 0 0 1 1 1c0 1.25.2 2.45.57 3.6a1 1 0 0 1-.25 1z"/></svg>
      </p>
      <p class="contact__line">dale.morven@plivorantu.com
        <svg class="contact__icon" viewBox="0 0 24 24" aria-hidden="true"><rect x="2" y="5" width="20" height="14" rx="2" fill="none" stroke="#f0892a" stroke-width="2.4"/><path d="M3 6l9 7 9-7" fill="none" stroke="#f0892a" stroke-width="2.4"/></svg>
      </p>
    </div>
  </section>

</body>
</html>
```